Give Gold Kite an Online Presence!

Gold Kite Property Maintenance is an Australian Owned property maintenance company who needs a stand out online presence.

GK maintains many buildings and sites and wants to appeal to a corporate professional market with their brand new website. GK is essentially a handyman service offering all maintenance services to home owners, office managers, real estate agents and strata managers.

The Website:
We need a corporate website that appeals to our broader customer base (property owners, property managers, office managers) the copy is being written by a professional so use filler text for now.

Things that we want:
Home page that sets us apart and appeals to the corporate and residential market. The home page needs to not focus on either the residential or commercial market. The home page should focus on our logo and branding. We have a logo already and it is attached to the brief, please use it and try to consider the colour pallette that goes with it. Whilst we want the site to appear strong and manly it is important to remember that 95% of our customers are female so we need the site to be appealing to women. Women need to believe that we are strong, dependable and trustworthy.
We'd like a quote page and potentially also the ability to get a quote from the home page (please don't put it in if it ruins the overall feel of the home page)
An "about us" page
A contact us page
A blog that's built in (we don't want to link to an external blog)
(overall we'd expect to have 6 or 7 pages total)

The site will also need coding - we expect this to be done in a separate project but need you to consider a few things about the coding side of things.

It needs to be iPhone and iPad compatible.

We'd like you to suggest the best CMS that you would use or if you would suggest not using a CMS please let us know with your submissions.

Target Market(s)

Property owners, office managers and property managers who need maintenance on buildings (So all of them)

Industry/Entity Type

Property Maintenance

Requirements
Must have
• Our Logo
Home page
About Us
Residential
Commercial
Real Estate/Strata
Contact Us/Quote
Blog
Nice to have
• Quote form included in home page
Movement on the home page at least
Should not have
• other logos, too much colour
NO FLASH

```html
<!DOCTYPE html>
<html lang="en">
<head>
<meta charset="utf-8">
<title>Gold Kite Property Maintenance</title>
<link rel="stylesheet" href="https://fonts.googleapis.com/css2?family=Arimo:ital,wght@0,400;0,700;1,400&family=Roboto:wght@300;400&display=swap">
<style>
  :root {
    --blue: #1a7fe6;
    --blue-deep: #0f6fd6;
    --charcoal: #4a4a4a;
    --charcoal-dark: #333333;
    --orange: #f7a21c;
    --orange-light: #ffc04a;
    --heading-blue: #2a7ab8;
    --text: #4a4a4a;
    --muted: #777777;
    --rule: #6f6f6f;
    --white: #ffffff;
  }
  * { box-sizing: border-box; margin: 0; padding: 0; }
  html, body { width: 1200px; height: 623px; overflow: hidden; background: var(--white); }
  body { position: relative; font-family: "Arimo", Arial, sans-serif; color: var(--text); }

  .top-strip { position: absolute; left: 112px; top: 0; width: 960px; height: 18px;
    background: linear-gradient(90deg, var(--blue) 0 70%, var(--charcoal) 82%); }

  .main-nav { position: absolute; left: 112px; top: 18px; width: 960px; height: 42px; background: var(--white); }
  .main-nav a { position: absolute; top: 0; height: 42px; line-height: 42px; font-size: 12px;
    color: #333; text-decoration: none; letter-spacing: .1px; }
  .main-nav .sep { position: absolute; top: 0; width: 1px; height: 42px; background: #d8d8d8; }
  .main-nav .current { color: var(--orange); }
  .badge-new { position: absolute; left: 706px; top: 14px; width: 30px; height: 15px; border-radius: 8px;
    background: #1a6cc0; color: var(--white); font-size: 9px; font-weight: 700; text-align: center; line-height: 15px; }
  .search-zone { position: absolute; left: 792px; top: 0; width: 168px; height: 42px;
    background: linear-gradient(180deg, #f2f2f2, #e2e2e2); }
  .search-field { position: absolute; left: 8px; top: 7px; width: 126px; height: 27px; background: var(--white);
    border: 1px solid #c8c8c8; font-size: 11px; font-style: italic; color: #555; padding-left: 8px; line-height: 25px; }
  .search-icon { position: absolute; left: 144px; top: 14px; }

  .hero { position: absolute; left: 112px; top: 60px; width: 960px; height: 244px; overflow: hidden; }
  .hero-bg { position: absolute; inset: 0; }
  .brand-name { position: absolute; left: 30px; top: 172px; width: 200px; color: var(--white);
    font-weight: 700; text-align: center; line-height: 1.1; }
  .brand-name .line-1 { display: block; font-size: 22px; }
  .brand-name .line-2 { display: block; font-size: 13px; }
  .tagline { position: absolute; left: 272px; top: 55px; color: var(--white); }
  .tagline .big { font-size: 86px; font-weight: 700; line-height: 1; letter-spacing: 1px; }
  .tagline .sub { font-size: 17px; font-weight: 700; margin-top: 2px; }
  .tagline .sub-2 { font-size: 16px; font-style: italic; margin-top: 2px; }

  .quote-card { position: absolute; left: 720px; top: 23px; width: 214px; height: 122px; border-radius: 8px;
    background: #2a2a2a; }
  .quote-card::after { content: ""; position: absolute; left: 98px; top: 122px; border: 7px solid transparent;
    border-top-color: #2a2a2a; }
  .quote-inner { position: absolute; left: 7px; top: 7px; width: 200px; height: 108px; border-radius: 5px;
    background: linear-gradient(180deg, #ffffff, #bdbdbd); }
  .quote-title { text-align: center; font-size: 12px; font-weight: 700; color: #333; margin-top: 6px; }
  .quote-input { position: absolute; left: 12px; width: 174px; height: 30px; border-radius: 6px; background: var(--white);
    border: 1px solid #cfcfcf; font-size: 11px; font-style: italic; color: #666; padding-left: 9px; line-height: 28px; }
  .request-btn { position: absolute; left: 723px; top: 182px; width: 201px; height: 35px; border-radius: 18px;
    background: linear-gradient(180deg, var(--orange-light), var(--orange)); color: var(--white);
    font-size: 16px; font-weight: 700; text-align: center; line-height: 35px; letter-spacing: .3px; }

  .hero-shadow { position: absolute; left: 130px; top: 304px; width: 930px; height: 14px;
    background: radial-gradient(ellipse at top, rgba(0,0,0,.22), rgba(0,0,0,0) 70%); }

  .content { position: absolute; left: 112px; top: 334px; width: 952px; }
  .page-title { font-family: "Roboto", Arial, sans-serif; font-weight: 300; font-size: 33px; color: var(--heading-blue); }
  .body-copy { font-size: 11.6px; line-height: 14.6px; text-align: justify; color: var(--text); }
  .intro { position: absolute; top: 56px; width: 952px; }
  .section-heading { position: absolute; left: -4px; top: 117px; width: 960px; height: 28px; }
  .section-heading::before, .section-heading::after { content: ""; position: absolute; top: 12px; width: 202px;
    height: 2px; background: var(--rule); }
  .section-heading::before { left: 0; } .section-heading::after { right: 0; }
  .section-heading h2 { text-align: center; font-family: "Roboto", Arial, sans-serif; font-weight: 300;
    font-size: 23px; color: var(--muted); line-height: 26px; }
  .detail { position: absolute; top: 159px; width: 952px; }
  .closing-rule { position: absolute; left: 109px; top: 570px; width: 960px; height: 1px; background: #c9c9c9; }
  .closing-rule::after { content: ""; position: absolute; left: 20px; right: 20px; top: 1px; height: 10px;
    background: radial-gradient(ellipse at top, rgba(0,0,0,.08), rgba(0,0,0,0) 70%); }
</style>
</head>
<body>
  <div class="top-strip"></div>

  <nav class="main-nav">
    <a class="current" style="left:18px">START</a>
    <span class="sep" style="left:70px"></span>
    <a style="left:89px">ABOUT US</a>
    <span class="sep" style="left:167px"></span>
    <a style="left:185px">RESIDENTIAL</a>
    <span class="sep" style="left:275px"></span>
    <a style="left:292px">COMMERCIAL</a>
    <span class="sep" style="left:386px"></span>
    <a style="left:401px">REAL ESTATE/STRATA</a>
    <span class="sep" style="left:541px"></span>
    <a style="left:560px">CONTACT US/QUOTE</a>
    <span class="sep" style="left:690px"></span>
    <span class="badge-new">NEW</span>
    <a style="left:745px">BLOG</a>
    <div class="search-zone">
      <div class="search-field">Search...</div>
      <svg class="search-icon" width="14" height="14" viewBox="0 0 14 14" aria-hidden="true">
        <circle cx="5.5" cy="5.5" r="4" fill="none" stroke="#2a7ab8" stroke-width="2"/>
        <line x1="8.5" y1="8.5" x2="12.5" y2="12.5" stroke="#2a7ab8" stroke-width="2.4" stroke-linecap="round"/>
      </svg>
    </div>
  </nav>

  <section class="hero">
    <svg class="hero-bg" width="960" height="244" viewBox="0 0 960 244" aria-hidden="true">
      <defs>
        <linearGradient id="heroBlue" x1="0" y1="0" x2="0" y2="1">
          <stop offset="0" stop-color="#1a84ec"/><stop offset="1" stop-color="#1470d4"/>
        </linearGradient>
        <linearGradient id="heroGrey" x1="0" y1="0" x2="1" y2="1">
          <stop offset="0" stop-color="#555"/><stop offset="1" stop-color="#3c3c3c"/>
        </linearGradient>
      </defs>
      <rect width="960" height="244" fill="url(#heroBlue)"/>
      <path d="M686 0 C640 40 665 90 662 130 C658 180 626 205 634 244 L960 244 L960 0 Z" fill="url(#heroGrey)"/>
      <path d="M686 0 C640 40 665 90 662 130 C658 180 626 205 634 244" fill="none" stroke="#2a2a2a" stroke-width="4" opacity=".5"/>
    </svg>

    <div class="brand-name">
      <span class="line-1">GOLD KITE</span>
      <span class="line-2">PROPERTY MAINTENANCE</span>
    </div>

    <div class="tagline">
      <div class="big">SIMPLY</div>
      <div class="sub">THE BEST PROPERTY MAINTENANCE</div>
      <div class="sub-2">YOU CAN GET ANYWHERE</div>
    </div>

    <div class="quote-card">
      <div class="quote-inner">
        <div class="quote-title">Request a quote now!</div>
        <div class="quote-input" style="top:28px">Your E-mail</div>
        <div class="quote-input" style="top:66px">Your Property type</div>
      </div>
    </div>
    <div class="request-btn">REQUEST QUOTE</div>
  </section>
  <div class="hero-shadow"></div>

  <main class="content">
    <h1 class="page-title">ABOUT US</h1>
    <p class="body-copy intro">Lorem ipsum dolor sit amet, consectetur adipisicing elit. Proin nibh augue, suscipit a, scelerisque sed, lacinia in, mi. Cras vel lorem. Etiam pellentesque aliquetLorem ipsum dolor sit amet, consectetur adipisicing elit. Proin nibh augue, suscipit a, scelerisque sed, lacinia in, mi. Cras vel lorem. Etiam pellentesque aliquetLorem ipsum dolor sit amet, consectetur adipisicing elit. Proin nibh augue, suscipit a, scelerisque sed, lacinia in, mi. Cras vel lorem. Etiam pellentesque aliquetLorem ipsum dolor sit amet, consectetur adipisicing elit. Proin nibh</p>
    <div class="section-heading"><h2>LOREM IPSUM DOLOR SIT AM CONTESTADUR</h2></div>
    <p class="body-copy detail">Lorem ipsum dolor sit amet, consectetur adipisicing elit. Proin nibh augue, suscipit a, scelerisque sed, lacinia in, mi. Cras vel lorem. Etiam pellentesque aliquetLorem ipsum dolor sit amet, consectetur adipisicing elit. Proin nibh augue, suscipit a, scelerisque sed, lacinia in, mi. Cras vel lorem. Etiam pellentesque aliquetLorem ipsum dolor sit amet, consectetur adipisicing elit. Proin nibh augue, suscipit a, scelerisque sed, lacinia in, mi. Cras vel lorem. Etiam pellentesque aliquetLorem ipsum dolor sit amet, consectetur adipisicing elit. Proin nibh</p>
  </main>
  <div class="closing-rule"></div>
</body>
</html>
```